Business cards and stationary design

We just completed the design of our new logo and we need to print new business cards and letterhead for our nonprofit. We are looking for a fresh new design that shows off our new logo. On letterhead, we must have a column on the right or left to include our Board of Directors (up to 45 names) (see attachment)

Industry/Entity Type

Non-Profit

Contact Information for Business Card

Standard business card with name, title, Company name, mailing address phone numbers, email address and website. Tagline on back "Every family deserves a home"

Font styles to use
Sans Serif

Requirements
Must have
• include pertinent information above
• new logo
• fonts compatible with logo
• should use logo colors only
Nice to have
• tag lines

```html
<!DOCTYPE html>
<html lang="en">
<head>
<meta charset="utf-8">
<title>Shelter Path Center – Business Card</title>
<link href="https://fonts.googleapis.com/css2?family=Source+Sans+3:wght@400;600&family=Courier+Prime:wght@700&display=swap" rel="stylesheet">
<style>
  :root {
    --bg: #ece9e6;
    --white: #ffffff;
    --red: #ec1c24;
    --yellow: #fbb62b;
    --teal: #0f7d95;
    --teal-card: #0a84a0;
    --text-sans: "Source Sans 3", Arial, sans-serif;
    --text-mono: "Courier Prime", "Courier New", monospace;
  }
  * { box-sizing: border-box; margin: 0; padding: 0; }
  html, body { width: 1200px; height: 900px; overflow: hidden; }
  body { background: var(--bg); font-family: var(--text-sans); position: relative; }

  .card { position: absolute; overflow: hidden; box-shadow: 0 4px 14px rgba(0,0,0,.18); }

  /* Front */
  .card-front { left: 177px; top: 73px; width: 589px; height: 364px; background: var(--white); }
  .front-bands { position: absolute; left: 0; top: 0; }
  .brand { position: absolute; display: flex; align-items: center; gap: 14px; }
  .card-front .brand { left: 84px; top: 62px; }
  .brand-mark { width: 46px; height: 46px; background: var(--teal); }
  .brand-name { font-family: var(--text-sans); font-weight: 400; font-size: 38px; color: var(--teal); letter-spacing: .5px; line-height: 1; }

  .contact-list { position: absolute; left: 45px; top: 271px; list-style: none; color: var(--white); font-size: 16px; line-height: 21px; }
  .contact-list li { display: flex; align-items: center; gap: 6px; }
  .contact-list svg { width: 12px; height: 12px; fill: var(--white); }

  .person { position: absolute; right: 36px; top: 231px; text-align: right; color: var(--white); }
  .person-name { font-weight: 600; font-size: 20px; line-height: 25px; }
  .person-title { font-size: 16px; line-height: 20px; }
  .person-address { margin-top: 17px; font-size: 16px; line-height: 21px; font-style: normal; }

  /* Back */
  .card-back { left: 388px; top: 505px; width: 567px; height: 352px; background: var(--teal-card); }
  .card-back .brand { left: 0; right: 0; top: 86px; flex-direction: column; gap: 26px; }
  .card-back .brand-mark { width: 70px; height: 70px; background: var(--white); }
  .card-back .brand-name { color: var(--white); font-size: 42px; }
  .tagline { position: absolute; left: 0; right: 0; top: 284px; text-align: center; font-family: var(--text-mono); font-weight: 700; font-size: 18px; color: var(--white); letter-spacing: .6px; }
</style>
</head>
<body>

<section class="card card-front" aria-label="Business card front">
  <svg class="front-bands" width="589" height="364" viewBox="0 0 589 364" aria-hidden="true">
    <polygon points="0,189 331,189 313,216 0,216" fill="var(--yellow)"/>
    <polygon points="345,182 589,182 589,364 0,364 0,220 316,220" fill="var(--red)"/>
  </svg>

  <div class="brand">
    <span class="brand-mark"></span>
    <span class="brand-name">shelter path center</span>
  </div>

  <ul class="contact-list">
    <li><svg viewBox="0 0 24 24"><path d="M6.6 10.8a15 15 0 0 0 6.6 6.6l2.2-2.2a1 1 0 0 1 1-.25 11.4 11.4 0 0 0 3.6.57 1 1 0 0 1 1 1V20a1 1 0 0 1-1 1A17 17 0 0 1 3 4a1 1 0 0 1 1-1h3.5a1 1 0 0 1 1 1c0 1.250.2 2.450.57 3.6a1 1 0 0 1-.25 1z"/></svg>044-555 010 200</li>
    <li><svg viewBox="0 0 24 24"><path d="M2 5h20v14H2z M2 5l10 8 10-8" fill="var(--white)" stroke="var(--red)" stroke-width="2"/></svg>hello@shelterpath.org</li>
    <li><svg viewBox="0 0 24 24"><circle cx="12" cy="12" r="10" fill="none" stroke="var(--white)" stroke-width="2"/><path d="M2 12h20M12 2c3 3 3 17 0 20M12 2c-3 3-3 17 0 20" fill="none" stroke="var(--white)" stroke-width="2"/></svg>www.shelterpath.org</li>
  </ul>

  <div class="person">
    <p class="person-name">DANIEL REYES</p>
    <p class="person-title">Managing Director</p>
    <address class="person-address">12345, Address Goes Here<br>Name here, 123456</address>
  </div>
</section>

<section class="card card-back" aria-label="Business card back">
  <div class="brand">
    <span class="brand-mark"></span>
    <span class="brand-name">shelter path center</span>
  </div>
  <p class="tagline">Every family deserves a home</p>
</section>

</body>
</html>
```